Ecard for facebook and Instagram postings

I need 4 ecards (don't know if that is what it is called) for Facebook and Instagram postings. My Logo and company name should be incorporated and also be square. I would like to be able to insert text as I need. Examples are:

https://www.plorvexa.com/photo.php?fbid=20262841672382489&set=a.20261729249182489.516031.71298967488&type=1&relevant_count=1

https://media-a-kpt.yy.plorvexacdn.net/hpics-bmk4/2345967_657092986477056_308792573_n.jpg

I don't necessarily need images on them, just the color scheme to my business cards and the logo and business name. But if you'd like to give it an interesting look, you can go ahead and play with it. My site is tornquillmentoring.com, if you'd like to see the style of it.

Thank you!!!
Updates

I just uploaded the logo in two variations.  Thank you!

Target Market(s)

Women 16-65

Industry/Entity Type

Business

Requirements
Must have
• Logo and business name
Should not have
• No white background. I have attached business card picture so you can have an idea of what I'd like.

```html
<!DOCTYPE html>
<html lang="en">
<head>
<meta charset="utf-8">
<title>Tornquill Mentoring – Quote Card</title>
<link rel="stylesheet" href="https://fonts.googleapis.com/css2?family=Tinos:wght@700&family=Montserrat:wght@500;600&display=swap">
<style>
  :root {
    --accent-orange: #f39a1e;
    --quote-red: #c0272d;
    --card-bg-light: #f4f4f4;
    --card-bg-mid: #e3e3e3;
    --ink: #0c0c0c;
    --band-black: #000000;
    --divider-grey: #8a8a8a;
    --band-red: #c0272d;
    --white: #ffffff;
  }
  * { margin: 0; padding: 0; box-sizing: border-box; }
  html, body { width: 1200px; height: 1200px; overflow: hidden; }
  body { background: var(--card-bg-light); }

  .card {
    position: relative;
    width: 1200px;
    height: 1200px;
    overflow: hidden;
    background: radial-gradient(circle at 50% 45%, var(--card-bg-light) 0%, var(--card-bg-mid) 100%);
  }
  .top-bar {
    position: absolute; left: 0; top: 0;
    width: 100%; height: 20px;
    background: var(--accent-orange);
  }
  .quote-mark {
    position: absolute;
    font-family: "Tinos", "Times New Roman", serif;
    font-weight: 700;
    color: var(--quote-red);
    font-size: 300px;
    line-height: 1;
  }
  .quote-mark--open { left: 55px; top: 50px; }
  .quote-mark--close { right: 70px; top: 800px; }

  .quote-text {
    position: absolute;
    left: 0; top: 215px;
    width: 100%;
    text-align: center;
    font-family: "Tinos", "Times New Roman", serif;
    font-weight: 700;
    font-size: 104px;
    line-height: 128px;
    color: var(--ink);
  }

  .footer {
    position: absolute; left: 0; top: 993px;
    width: 100%; height: 207px;
    background: var(--band-black);
    border-top: 7px solid var(--divider-grey);
  }
  .footer__stripe {
    position: absolute; left: 0; bottom: 0;
    width: 100%; height: 25px;
    background: var(--band-red);
  }
  .brand-name {
    position: absolute; left: 32px; top: 12px;
    font-family: "Tinos", "Times New Roman", serif;
    font-weight: 700;
    font-size: 78px;
    color: var(--white);
    line-height: 1;
  }
  .brand-tagline {
    position: absolute; left: 34px; top: 110px;
    font-family: "Montserrat", Arial, sans-serif;
    font-weight: 500;
    font-size: 25px;
    letter-spacing: 7px;
    color: var(--white);
  }
  .brand-url {
    position: absolute; left: 540px; top: 110px;
    font-family: "Montserrat", Arial, sans-serif;
    font-weight: 600;
    font-size: 25px;
    letter-spacing: 2px;
    color: var(--white);
  }
  .brand-dot {
    position: absolute; left: 995px; top: 8px;
    width: 160px; height: 160px;
  }
</style>
</head>
<body>
  <main class="card">
    <div class="top-bar"></div>

    <span class="quote-mark quote-mark--open" aria-hidden="true">&ldquo;</span>

    <p class="quote-text">
      Ignorance is the<br>
      curse of God;<br>
      knowledge is the<br>
      wing wherewith we<br>
      fly to heaven
    </p>

    <span class="quote-mark quote-mark--close" aria-hidden="true">&rdquo;</span>

    <footer class="footer">
      <div class="brand-name">Tornquill</div>
      <div class="brand-tagline">MENTORING SERVICES</div>
      <div class="brand-url">TORNQUILLMENTORING.COM</div>
      <svg class="brand-dot" viewBox="0 0 160 160" aria-hidden="true">
        <circle cx="80" cy="80" r="74" fill="var(--accent-orange)" stroke="var(--white)" stroke-width="5"/>
      </svg>
      <div class="footer__stripe"></div>
    </footer>
  </main>
</body>
</html>
```